BOLD & MINIMALIST DESIGN NEEDED

We want a very bold but minimalistic business card design that is impactful and utilizes both sides of the business card. Our current logo is included for your use.

We want bold fonts and good use of negative space. We don't want the logo to overpower the design.

Target Market(s)

Professionals who are building new commercial buildings.

Industry/Entity Type

Construction

Contact Information for Business Card

Name, Title, email, office phone, cell phone, website

Font styles to use
Serif
Sans Serif

Requirements
Must have
• Bold design!

```html
<!DOCTYPE html>
<html lang="en">
<head>
<meta charset="utf-8">
<title>Ridgeline Design + Build — Business Card</title>
<link rel="stylesheet" href="https://fonts.googleapis.com/css2?family=Archivo:wght@400;500;800&display=swap">
<style>
  :root {
    --backdrop: #e9e9ea;
    --card: #f4f4f4;
    --ink: #151515;
    --ink-soft: #2b2b2b;
    --accent: #6fd63a;
    --card-shadow: 0 18px 40px rgba(0,0,0,0.14), 0 3px 8px rgba(0,0,0,0.08);
  }
  * { box-sizing: border-box; margin: 0; padding: 0; }
  html, body {
    width: 1200px; height: 988px; overflow: hidden;
    background: var(--backdrop);
    font-family: "Archivo", Arial, sans-serif;
    color: var(--ink);
  }
  .canvas {
    width: 1200px; height: 988px;
    display: flex; align-items: center; justify-content: center; gap: 60px;
  }
  .card {
    width: 520px; height: 298px;
    background: var(--card);
    box-shadow: var(--card-shadow);
    position: relative;
  }

  /* Wordmark: one colour, one weight, with one plain square */
  .wordmark {
    display: flex; align-items: center; gap: 12px;
    font-weight: 800; color: var(--ink); text-transform: uppercase;
  }
  .wordmark__square { background: var(--accent); flex: none; }
  .wordmark__text { display: flex; flex-direction: column; line-height: 1; }
  .wordmark__name { letter-spacing: 0.01em; }
  .wordmark__tag { letter-spacing: 0.32em; margin-top: 6px; }

  /* Front side */
  .card--front { display: flex; align-items: center; padding: 0 34px 0 40px; }
  .card--front .wordmark { width: 240px; }
  .card--front .wordmark__square { width: 18px; height: 18px; }
  .card--front .wordmark__name { font-size: 30px; }
  .card--front .wordmark__tag { font-size: 10px; }

  .contact { margin-left: 30px; }
  .contact__name { font-size: 18px; font-weight: 800; }
  .contact__title { font-size: 13px; font-weight: 400; color: var(--ink-soft); margin-top: 2px; }
  .contact__list { list-style: none; margin-top: 22px; }
  .contact__item {
    display: flex; align-items: center; gap: 9px;
    font-size: 13px; font-weight: 400; margin-top: 7px;
  }
  .contact__icon {
    width: 18px; height: 18px; border-radius: 50%;
    background: var(--ink); display: flex; align-items: center; justify-content: center;
    flex: none;
  }
  .contact__icon svg { width: 11px; height: 11px; }

  /* Back side */
  .card--back { display: flex; align-items: center; justify-content: center; }
  .card--back .wordmark { gap: 18px; }
  .card--back .wordmark__square { width: 30px; height: 30px; }
  .card--back .wordmark__name { font-size: 48px; }
  .card--back .wordmark__tag { font-size: 14px; margin-top: 8px; }
  .card--back .rule { position: absolute; left: 100px; right: 100px; bottom: 78px; height: 1px; background: var(--ink); }
</style>
</head>
<body>
<main class="canvas">

  <section class="card card--front" aria-label="Card front">
    <div class="wordmark">
      <span class="wordmark__square"></span>
      <span class="wordmark__text">
        <span class="wordmark__name">Ridgeline</span>
        <span class="wordmark__tag">Design + Build</span>
      </span>
    </div>

    <div class="contact">
      <p class="contact__name">Jonah Whitfield</p>
      <p class="contact__title">Engineer + Founder</p>
      <ul class="contact__list">
        <li class="contact__item">
          <span class="contact__icon">
            <svg viewBox="0 0 12 12"><path d="M2.5 1h2l1 2.6-1.3 1a6 6 0 0 0 3.2 3.2l1-1.3 2.6 1v2c0 .6-.4 1-1 1A9.5 9.5 0 0 1 1.5 2c0-.6.4-1 1-1z" fill="var(--accent)"/></svg>
          </span>555.214.3300
        </li>
        <li class="contact__item">
          <span class="contact__icon">
            <svg viewBox="0 0 12 12"><rect x="3" y="0.8" width="6" height="10.4" rx="1" fill="var(--accent)"/><rect x="4" y="2" width="4" height="6.5" fill="var(--ink)"/></svg>
          </span>555-214-3301
        </li>
        <li class="contact__item">
          <span class="contact__icon">
            <svg viewBox="0 0 12 12"><rect x="1" y="2.5" width="10" height="7" rx="0.8" fill="var(--accent)"/><path d="M1.3 3 6 6.6 10.7 3" fill="none" stroke="var(--ink)" stroke-width="1"/></svg>
          </span>info@ridgeline-db.com
        </li>
        <li class="contact__item">
          <span class="contact__icon">
            <svg viewBox="0 0 12 12"><circle cx="6" cy="6" r="4.8" fill="none" stroke="var(--accent)" stroke-width="1.2"/><ellipse cx="6" cy="6" rx="2" ry="4.8" fill="none" stroke="var(--accent)" stroke-width="1"/><path d="M1.2 6h9.6" stroke="var(--accent)" stroke-width="1"/></svg>
          </span>www.ridgeline-db.com
        </li>
      </ul>
    </div>
  </section>

  <section class="card card--back" aria-label="Card back">
    <div class="wordmark">
      <span class="wordmark__square"></span>
      <span class="wordmark__text">
        <span class="wordmark__name">Ridgeline</span>
        <span class="wordmark__tag">Design + Build</span>
      </span>
    </div>
    <span class="rule"></span>
  </section>

</main>
</body>
</html>
```